Marlowby Services Website Design

We have most content but require a professional design. We have a logo already and will need it utilized along with several of the photos from the attached documentation.
First page should have our mission and Vision and the synapsis provided in the word document. Visitors will be prompted to select from one of our 3 divisions from this page.
Each division will have the same list of tabs : About, Services, Safety, Careers and Contact.
Photos on each divisions page should be representative of the divisions offerings. The word doc attached contains the requested content and we are open to edits that would complement and fill the website.
I like the Quorvane site www.quorvane.example - they are our competition so cant be modeled directly after this.
Please include prompts to request quote at each service page. align the format of the geotechnical page to the other 2 divisions.
I used chat gpt for some of the content so will need it optimized for SCO.

```html
<!DOCTYPE html>
<html lang="en">
<head>
<meta charset="utf-8">
<title>Marlowby Services</title>
<link href="https://fonts.googleapis.com/css2?family=Roboto:wght@300;400;500;900&family=Racing+Sans+One&display=swap" rel="stylesheet">
<style>
:root{
  --red:#ea1c24;
  --ink:#111111;
  --white:#ffffff;
  --soil:#7a6447;
  --soil-dark:#3e3121;
  --mist:#e9ebed;
  --sky:#2f6fd0;
  --footer:#000000;
  --body:#222222;
}
*{margin:0;padding:0;box-sizing:border-box}
html,body{width:1200px;height:3060px;overflow:hidden;background:var(--white)}
body{position:relative;font-family:"Roboto",sans-serif;color:var(--body)}
.abs{position:absolute}
.display{font-family:"Racing Sans One","Roboto",sans-serif;font-style:italic;font-weight:400}
.accent{color:var(--red)}

/* header */
.site-header{left:0;top:0;width:1200px;height:78px;background:var(--white)}
.brand{font-weight:900;letter-spacing:6px;text-transform:uppercase;color:var(--red)}
.site-header .brand{left:113px;top:20px;font-size:38px;line-height:38px}
.main-nav a{position:absolute;top:36px;font-size:15px;color:var(--ink);text-decoration:none}
.login-btn{left:956px;top:24px;width:131px;height:39px;background:var(--red);clip-path:polygon(8% 0,100% 0,92% 100%,0 100%);color:var(--white);font-size:15px;display:flex;align-items:center;justify-content:center;gap:8px}

/* hero */
.hero{left:0;top:78px;width:1200px;height:642px;border-radius:0 0 150px 150px;background:linear-gradient(120deg,#8a7352 0%,var(--soil) 45%,#6b5738 100%);overflow:hidden}
.hero-shadow{left:160px;top:110px;width:620px;height:420px;background:radial-gradient(ellipse at center,rgba(40,30,20,.45),rgba(40,30,20,0) 70%)}
.hero-truck{left:720px;top:78px;width:345px;height:725px;border-radius:18px 18px 60px 60px;background:linear-gradient(180deg,#e9ecef 0%,#cfd4d8 60%,#9ea3a7 100%)}
.hero-kicker{left:113px;top:252px;font-size:21px;font-weight:300;color:var(--white)}
.hero-title{left:113px;top:286px;font-size:70px;line-height:70px;letter-spacing:9px;color:var(--white)}
.hero-text{left:113px;top:362px;width:400px;font-size:16px;line-height:29px;color:var(--white)}
.book-btn{left:113px;top:425px;width:178px;height:38px;background:var(--red);clip-path:polygon(10% 0,100% 0,90% 100%,0 100%);color:var(--white);font-size:15px;display:flex;align-items:center;justify-content:center}

/* services */
.section-title{font-size:40px;line-height:48px;text-align:center;color:var(--ink)}
.services-title{left:0;top:865px;width:1200px}
.mission-band{left:0;top:1188px;width:1200px;height:524px;background:linear-gradient(180deg,#dfe2e4 0%,var(--mist) 40%,#eef0f1 100%)}
.service-card{top:978px;height:330px;clip-path:polygon(8% 0,100% 0,92% 100%,0 100%);display:flex;align-items:flex-end;justify-content:center;padding-bottom:26px}
.service-card span{font-family:"Racing Sans One",sans-serif;font-style:italic;color:var(--white);font-size:22px;line-height:30px;text-align:center}
.card-street{left:110px;width:326px;background:linear-gradient(160deg,#a5a39b,#7e7a6e 60%,#4f4a40)}
.card-tower{left:436px;width:325px;background:linear-gradient(180deg,#3d7ad1,#6c92bd 60%,#40513e)}
.card-forest{left:761px;width:326px;background:linear-gradient(180deg,#86a76a,#4e6d3a 50%,#8c7d67)}
.arrow{width:30px;height:30px;border-radius:50%;display:flex;align-items:center;justify-content:center}
.arrow-prev{left:39px;top:1114px;background:#b8b8b8}
.arrow-next{left:1127px;top:1114px;background:var(--ink)}

.mission-title{left:0;top:1399px;width:1200px}
.mission-text{left:268px;top:1469px;width:670px;font-size:16px;line-height:30px;text-align:center;color:var(--body)}

/* vision */
.vision-back{left:113px;top:1815px;width:374px;height:401px;clip-path:polygon(4% 0,100% 0,100% 100%,0 100%);background:linear-gradient(180deg,#c9ced4 0%,#b6b9b4 45%,#8f8d85 100%)}
.vision-front{left:261px;top:1934px;width:291px;height:311px;border:5px solid var(--white);clip-path:polygon(3% 0,100% 0,97% 100%,0 100%);background:linear-gradient(180deg,#5f7a4b 0%,#e6e7e7 45%,#b3b6b8 100%)}
.vision-title{left:620px;top:1930px;width:490px}
.vision-text{left:640px;top:2007px;width:450px;font-size:16px;line-height:30px;text-align:center}

/* divisions */
.division{top:2349px;width:300px;height:253px;border-radius:22px;clip-path:polygon(5% 0,100% 0,95% 100%,0 100%)}
.div-aerial{left:112px;background:linear-gradient(180deg,#b8bfc6,#76786b 50%,#5a5c55)}
.div-geo{left:445px;background:linear-gradient(180deg,#3f7ddb,#9bb6d6 60%,#6d6f55)}
.div-renew{left:780px;background:linear-gradient(200deg,#2b62d2,#4d86e4 60%,#b9cbe8)}
.division-tag{top:2589px;height:38px;background:var(--red);clip-path:polygon(8% 0,100% 0,92% 100%,0 100%);color:var(--white);font-size:16px;display:flex;align-items:center;justify-content:center}

/* footer */
.site-footer{left:0;top:2721px;width:1200px;height:339px;background:var(--footer)}
.site-footer .brand{left:113px;top:2765px;font-size:50px;line-height:56px;letter-spacing:9px}
.social{top:2833px;width:33px;height:33px;border-radius:50%;background:var(--white)}
.copyright{left:113px;top:2883px;font-size:12px;color:var(--white)}
.footer-head{top:2769px;font-size:24px;color:var(--white)}
.footer-links a{position:absolute;left:550px;font-size:16px;color:var(--white);text-decoration:none}
.contact-icon{left:754px;width:52px;height:52px;border-radius:50%;background:var(--red);display:flex;align-items:center;justify-content:center}
.contact-line{left:813px;font-size:16px;color:var(--white)}
</style>
</head>
<body>

<header class="site-header abs">
  <div class="brand abs">Marlowby</div>
  <nav class="main-nav">
    <a style="left:440px">Home</a>
    <a style="left:523px">About Us</a>
    <a style="left:625px">Services</a>
    <a style="left:723px">Testimonials</a>
    <a style="left:850px">Contact Us</a>
  </nav>
  <div class="login-btn abs">Login
    <svg width="20" height="20" viewBox="0 0 20 20" fill="none" stroke="#fff" stroke-width="1.6"><path d="M9 4h7v12H9"/><path d="M2 10h10M9 7l3 3-3 3"/></svg>
  </div>
</header>

<section class="hero abs" role="img" aria-label="Aerial photo of a dirt work site with a service truck's shadow">
  <div class="hero-shadow abs" style="left:160px;top:30px"></div>
</section>
<div class="hero-truck abs" role="img" aria-label="Top-down photo of a white aerial boom truck"></div>
<div class="hero-kicker abs">WELCOME TO</div>
<div class="hero-title brand abs" style="color:var(--white)">Marlowby</div>
<p class="hero-text abs">Lorem ipsum dolor sit amet, consectetur adipiscing elit, sed do eiusmod tempor aliqua.</p>
<div class="book-btn abs">Book My Services</div>

<div class="mission-band abs" role="img" aria-label="Faded aerial photo of a small town"></div>
<h2 class="section-title services-title display abs">Marlowby <span class="accent">Services</span></h2>

<div class="service-card card-street abs" role="img" aria-label="Aerial view of a boom truck on a residential street"><span>Delivering Safe</span></div>
<div class="service-card card-tower abs" role="img" aria-label="Boom lift beside a water tower"><span>Reliable Aerial Access<br>And Maintenance<br>Services To Oil&amp;gas,</span></div>
<div class="service-card card-forest abs" role="img" aria-label="Aerial lift truck on a gravel road by a forest"><span>Construction</span></div>

<div class="arrow arrow-prev abs"><svg width="12" height="12" viewBox="0 0 12 12"><path d="M8 1 3 6l5 5" stroke="#fff" stroke-width="2.2" fill="none"/></svg></div>
<div class="arrow arrow-next abs"><svg width="12" height="12" viewBox="0 0 12 12"><path d="M4 1l5 5-5 5" stroke="#fff" stroke-width="2.2" fill="none"/></svg></div>

<h2 class="section-title mission-title display abs">Mission <span class="accent">Statement</span></h2>
<p class="mission-text abs">At Marlowby, our mission is to deliver unparalleled aerial access, geotechnical drilling, and service and maintenance solutions, consistently exceeding our clients' expectations. We strive to achieve this by investing in cutting-edge technology, fostering a culture of safety and continuous improvement, and prioritizing environmental sustainability. Through collaboration, integrity, and dedication, we aim to contribute to the success of our clients while maintaining the highest standards of quality and professionalism.</p>

<div class="vision-back abs" role="img" aria-label="Boom trucks parked on gravel near wind turbines"></div>
<div class="vision-front abs" role="img" aria-label="White aerial boom truck parked by trees"></div>
<h2 class="section-title vision-title display abs">Our <span class="accent">Vision</span></h2>
<p class="vision-text abs">To be the leading provider of aerial access, geotechnical drilling, and service solutions, setting the standard for excellence in safety, efficiency, and environmental stewardship.</p>

<div class="division div-aerial abs" role="img" aria-label="Worker in a raised bucket above a rural highway"></div>
<div class="division div-geo abs" role="img" aria-label="Drilling rig beside a water tower"></div>
<div class="division div-renew abs" role="img" aria-label="Boom reaching a wind turbine against blue sky"></div>
<div class="division-tag abs" style="left:157px;width:188px">Aerial Access</div>
<div class="division-tag abs" style="left:497px;width:188px">Geotechnical Drilling</div>
<div class="division-tag abs" style="left:798px;width:247px">Renewable Energy Services</div>

<footer class="site-footer abs"></footer>
<div class="brand abs" style="left:113px;top:2768px;font-size:50px;line-height:56px;letter-spacing:9px">Marlowby</div>
<div class="social abs" style="left:114px" aria-label="Social link"></div>
<div class="social abs" style="left:161px" aria-label="Social link"></div>
<div class="social abs" style="left:208px" aria-label="Social link"></div>
<div class="copyright abs">© 2024 &nbsp;Marlowby &nbsp;| &nbsp;All Rights Reserved.</div>

<div class="footer-head display abs" style="left:548px">Quick Links</div>
<nav class="footer-links">
  <a style="top:2822px">Home</a>
  <a style="top:2864px">About Us</a>
  <a style="top:2906px">Services</a>
  <a style="top:2948px">Testimonials</a>
  <a style="top:2991px">Contact Us</a>
</nav>

<div class="footer-head display abs" style="left:753px">Contact Us</div>
<div class="contact-icon abs" style="top:2814px"><svg width="22" height="22" viewBox="0 0 24 24" fill="#fff"><path d="M6.6 10.8a15 15 0 0 0 6.6 6.6l2.2-2.2a1 1 0 0 1 1-.25 11.4 11.4 0 0 0 3.6.57 1 1 0 0 1 1 1V20a1 1 0 0 1-1 1A17 17 0 0 1 3 4a1 1 0 0 1 1-1h3.5a1 1 0 0 1 1 1c0 1.25.2 2.45.57 3.57a1 1 0 0 1-.25 1z"/></svg></div>
<div class="contact-line abs" style="top:2830px">+(555) 014 2290</div>
<div class="contact-icon abs" style="top:2889px"><svg width="20" height="22" viewBox="0 0 24 24" fill="#fff"><path d="M12 2a7 7 0 0 0-7 7c0 5.3 7 13 7 13s7-7.7 7-13a7 7 0 0 0-7-7zm0 9.5A2.5 2.5 0 1 1 12 6.5a2.5 2.5 0 0 1 0 5z"/></svg></div>
<div class="contact-line abs" style="top:2905px">218 Ridgeway Road Alderbank AB T0X-4K1</div>
<div class="contact-icon abs" style="top:2964px"><svg width="22" height="18" viewBox="0 0 24 18" fill="#fff"><path d="M2 0h20a2 2 0 0 1 2 2v.5L12 9 0 2.5V2a2 2 0 0 1 2-2zm-2 5 12 6.5L24 5v11a2 2 0 0 1-2 2H2a2 2 0 0 1-2-2z"/></svg></div>
<div class="contact-line abs" style="top:2980px">info@marlowbyservices.example</div>

</body>
</html>
```